Front cover for our tenth anniversary show programme

To create an eye catching tenth anniversary front cover for our programme

Moonbrook presents DANCE! 2015

date of the show Sunday 3rd May 2015

Venue The Harwick Playhouse

please see the updated brief!

Reason: there hasn't been anything that is quite right

```html
<!DOCTYPE html>
<html lang="en">
<head>
<meta charset="utf-8">
<title>Moonbrook presents DANCE! 2015 – Programme Cover</title>
<link rel="stylesheet" href="https://fonts.googleapis.com/css2?family=Anton&family=Arimo:wght@700&display=swap">
<style>
  :root {
    --backdrop: #e4e5e6;
    --band: #262626;
    --title-white: #ffffff;
    --accent-pink: #ec3d92;
    --collage-magenta: #c0247a;
    --collage-purple: #5a2a7e;
    --collage-blue: #2c3f8c;
    --collage-red: #b5202e;
    --collage-pink: #e45aa8;
  }
  * { box-sizing: border-box; margin: 0; padding: 0; }
  html, body {
    width: 1200px;
    height: 850px;
    overflow: hidden;
    background: var(--backdrop);
  }
  .canvas {
    position: relative;
    width: 1200px;
    height: 850px;
  }
  .programme-cover {
    position: absolute;
    left: 380px;
    top: 30px;
    width: 440px;
    height: 790px;
    overflow: hidden;
    background: var(--band);
    box-shadow: 0 6px 18px rgba(0,0,0,0.18);
  }
  .photo-collage {
    position: absolute;
    left: 0;
    top: 0;
    width: 440px;
    height: 570px;
    background:
      linear-gradient(180deg, rgba(0,0,0,0) 70%, rgba(30,10,30,0.35) 100%),
      linear-gradient(160deg,
        var(--collage-red) 0%,
        var(--collage-magenta) 22%,
        var(--collage-blue) 38%,
        var(--collage-purple) 55%,
        var(--collage-red) 72%,
        var(--collage-pink) 100%);
  }
  .cover-title {
    position: absolute;
    left: 0;
    top: 0;
    width: 440px;
    height: 600px;
  }
  .cover-title text {
    font-family: "Anton", "Oswald", sans-serif;
    fill: var(--title-white);
  }
  .show-details {
    position: absolute;
    left: 53px;
    top: 622px;
    font-family: "Arimo", Arial, sans-serif;
    font-weight: 700;
    font-size: 13px;
    line-height: 22px;
  }
  .show-date { color: var(--title-white); }
  .show-venue { color: var(--accent-pink); }
  .company-mark {
    position: absolute;
    left: 240px;
    top: 640px;
    width: 175px;
    text-align: center;
    font-family: "Arimo", Arial, sans-serif;
    font-weight: 700;
  }
  .company-dot {
    display: block;
    width: 22px;
    height: 22px;
    margin: 0 auto 8px;
    border-radius: 50%;
    background: var(--accent-pink);
  }
  .company-name {
    font-size: 30px;
    line-height: 32px;
    color: var(--title-white);
  }
  .anniversary-tag {
    margin-top: 6px;
    font-size: 15px;
    line-height: 18px;
    color: var(--accent-pink);
  }
</style>
</head>
<body>
<main class="canvas">
  <section class="programme-cover">
    <div class="photo-collage" role="img" aria-label="Collage of stage photographs of young dancers performing in colourful costumes under pink, blue and red lights"></div>

    <svg class="cover-title" viewBox="0 0 440 600" aria-label="Moonbrook presents DANCE! 2015">
      <text x="46" y="158" font-size="85" textLength="340" lengthAdjust="spacingAndGlyphs">MOONBROOK</text>
      <text x="46" y="236" font-size="85" textLength="340" lengthAdjust="spacingAndGlyphs">PRESENTS</text>
      <text x="46" y="384" font-size="165" textLength="335" lengthAdjust="spacingAndGlyphs">DANCE</text>
      <text x="46" y="574" font-size="210" textLength="340" lengthAdjust="spacingAndGlyphs">2015</text>
    </svg>

    <div class="show-details">
      <p class="show-date">3rd May 2015</p>
      <p class="show-venue">Harwick Playhouse</p>
    </div>

    <div class="company-mark">
      <span class="company-dot"></span>
      <p class="company-name">Moonbrook</p>
      <p class="anniversary-tag">Celebrating Ten Years</p>
    </div>
  </section>
</main>
</body>
</html>
```